Construction material supplies company business card ****

1. Full company name “K T Masonry Works Ltd”
I am after a Business card design for the company as a whole. We are better known in Solomon Islands as “K T Masonry” for short.

We are a building materials supplier of
Ready Mixed Concrete, Bricks and Blocks,
Quarry products- gravel, aggregates, sand etc.
Cement distributor/retailer of reputable brands.
Other prefab concrete products. Culverts, wave breakers, concrete retaining blocks etc.

2. Competitive Advantage over Competition: Quality, efficient, professional, dependable, reliable

3. We want people to feel trust worthy, high quality, strong when they see our brand

5. No preference to color. Maybe more sturdy and corporate. Not fancy.

Industry/Entity Type

CONSTRUCTION SUPPLY

Contact Information for Business Card

Name, Position, office phone mob phone, email

Requirements
Must have
• the company logo
Nice to have
• would like to see a mixture of designs, of with logo only and also with simple graphic designs to bring out the company whilst still have the strong sturdy professional feeling

```html
<!DOCTYPE html>
<html lang="en">
<head>
<meta charset="utf-8">
<title>K T Masonry – Business Card</title>
<link href="https://fonts.googleapis.com/css2?family=Michroma&family=Montserrat:wght@400;600&family=Roboto:wght@400&display=swap" rel="stylesheet">
<style>
  :root {
    --backdrop: #2b2b2d;
    --navy: #17426a;
    --navy-deep: #123758;
    --white: #ffffff;
    --ink: #222831;
    --muted: #6b7280;
    --rule: #e3e6ea;
    --ghost: #e4e9ef;
  }
  * { margin: 0; padding: 0; box-sizing: border-box; }
  html, body {
    width: 1200px; height: 900px; overflow: hidden;
    background: var(--backdrop);
  }
  .canvas {
    width: 1200px; height: 900px;
    display: flex; flex-direction: column; align-items: center; justify-content: center;
    gap: 36px;
  }
  .card {
    position: relative;
    width: 700px; height: 400px;
    overflow: hidden;
    box-shadow: 0 14px 30px rgba(0,0,0,.45);
  }

  /* Front */
  .card-front {
    background: var(--navy);
    display: flex; align-items: center; justify-content: center;
  }
  .brand {
    display: flex; align-items: center; gap: 18px;
    font-family: "Michroma", sans-serif;
    letter-spacing: 2px;
    white-space: nowrap;
  }
  .brand-mark { width: 34px; height: 34px; flex: none; }
  .card-front .brand { color: var(--white); font-size: 40px; }
  .card-front .brand-mark { background: var(--white); }

  /* Back */
  .card-back { background: var(--white); }
  .card-back .brand {
    position: absolute; left: 56px; top: 56px;
    flex-direction: column; gap: 14px;
    color: var(--navy); font-size: 30px; line-height: 1;
  }
  .card-back .brand-mark { background: var(--navy); width: 40px; height: 40px; }
  .holder {
    position: absolute; right: 52px; top: 92px; text-align: right;
    font-family: "Montserrat", sans-serif;
  }
  .holder-name {
    color: var(--navy); font-weight: 600; font-size: 24px;
    padding-bottom: 4px; border-bottom: 1px solid var(--rule);
  }
  .holder-role { color: var(--muted); font-size: 14px; margin-top: 2px; }
  .divider {
    position: absolute; left: 56px; right: 52px; top: 168px;
    height: 1px; background: var(--rule);
  }
  .divider-lower { top: 228px; right: 300px; }
  .ghost-square {
    position: absolute; right: 44px; bottom: 34px;
    width: 150px; height: 150px;
    border: 22px solid var(--ghost);
  }
  .contacts {
    position: absolute; left: 66px; top: 258px;
    list-style: none;
    font-family: "Roboto", sans-serif; font-size: 19px; color: var(--ink);
  }
  .contacts li { display: flex; align-items: center; gap: 18px; height: 27px; }
  .contacts svg { width: 16px; height: 16px; fill: var(--navy); flex: none; }
  .edge-band {
    position: absolute; left: 0; right: 0; bottom: 0; height: 8px;
    background: var(--navy-deep);
  }
</style>
</head>
<body>
<main class="canvas">
  <section class="card card-front">
    <div class="brand"><span class="brand-mark"></span><span class="brand-name">K T MASONRY</span></div>
  </section>

  <section class="card card-back">
    <div class="brand"><span class="brand-mark"></span><span class="brand-name">K T MASONRY</span></div>
    <div class="holder">
      <p class="holder-name">Peter Tovua</p>
      <p class="holder-role">Director</p>
    </div>
    <div class="divider"></div>
    <div class="divider divider-lower"></div>
    <div class="ghost-square"></div>
    <ul class="contacts">
      <li><svg viewBox="0 0 24 24" aria-hidden="true"><path d="M6.6 10.8a15.1 15.1 0 0 0 6.6 6.6l2.2-2.2a1 1 0 0 1 1-.25 11.4 11.4 0 0 0 3.6.57 1 1 0 0 1 1 1V20a1 1 0 0 1-1 1A17 17 0 0 1 3 4a1 1 0 0 1 1-1h3.5a1 1 0 0 1 1 1c0 1.25.2 2.450.57 3.6a1 1 0 0 1-.25 1z"/></svg>123 456 7890</li>
      <li><svg viewBox="0 0 24 24" aria-hidden="true"><path d="M7 1h10a2 2 0 0 1 2 2v18a2 2 0 0 1-2 2H7a2 2 0 0 1-2-2V3a2 2 0 0 1 2-2zm0 3v14h10V4zm5 15.5a1 1 0 1 0 0 2 1 1 0 0 0 0-2z"/></svg>123 456 7890</li>
      <li><svg viewBox="0 0 24 24" aria-hidden="true"><path d="M2 5h20v14H2zm2 2v.5l8 5 8-5V7zm0 2.8V17h16V9.8l-8 5z"/></svg>info@ktmasonry.com</li>
      <li><svg viewBox="0 0 24 24" aria-hidden="true"><path d="M12 2a10 10 0 1 0 0 20 10 10 0 0 0 0-20zm-1 17.9A8 8 0 0 1 4.1 11H7v2l4 2zm6.9-2.9A2 2 0 0 0 16 15.6V13h-5v-3h2V8h2V5.5A8 8 0 0 1 17.9 17z"/></svg>www.ktmasonry.com</li>
    </ul>
    <div class="edge-band"></div>
  </section>
</main>
</body>
</html>
```